Business Card Design for company

We want new business cards. We'd like something different-- yet still highly professional. Our tagline is Providing leadership, delivering success. Stock photos are ok, as long as they are relevant and look upscale.

Target Market(s)

Architecture/Business Management Consulting/Engineering Consulting

Contact Information for Business Card

dark gray background with pops of blue might be good, but you tell me. You're the designers. Rounded corners might be nice, but again, you tell me.

Font styles to use
Serif
Sans Serif

Colors
3276b5
5c5c5c
9d9d9d
fbfbfb

Requirements
Nice to have
• Something different, but still very professional.

```html
<!DOCTYPE html>
<html lang="en">
<head>
<meta charset="utf-8">
<title>Halvern Consulting – Business Card</title>
<link rel="stylesheet" href="https://fonts.googleapis.com/css2?family=Montserrat:wght@400;600;700&family=Open+Sans:wght@400;600&display=swap">
<style>
  :root {
    --stage: #1a1a1a;
    --card: #3c3d3f;
    --card-map: #47484a;
    --brand-blue: #3276b5;
    --band-blue: #2c6aa3;
    --text-light: #fbfbfb;
    --text-soft: #d6d6d6;
    --divider: #9d9d9d;
  }
  * { box-sizing: border-box; margin: 0; padding: 0; }
  html, body {
    width: 1200px; height: 900px; overflow: hidden;
    background: var(--stage);
  }
  .stage {
    width: 1200px; height: 900px;
    display: flex; flex-direction: column;
    align-items: center; justify-content: center; gap: 44px;
  }
  .card {
    position: relative;
    width: 620px; height: 354px;
    background: var(--card);
    border-radius: 6px;
    overflow: hidden;
    box-shadow: 0 12px 30px rgba(0,0,0,.55);
    color: var(--text-light);
  }
  .map-area {
    position: absolute; inset: 30px 40px 60px 40px;
    border-radius: 40% 50% 45% 40%;
    background: radial-gradient(ellipse at center, var(--card-map) 0%, rgba(71,72,74,0) 70%);
  }
  /* Front */
  .card-front .front-content {
    position: absolute; inset: 0;
    display: flex; flex-direction: column;
    align-items: center; justify-content: center; gap: 26px;
  }
  .brand-name {
    font-family: "Montserrat", sans-serif;
    font-weight: 600;
    color: var(--text-light);
    letter-spacing: 3px;
    text-transform: uppercase;
  }
  .card-front .brand-name { font-size: 34px; }
  .tagline {
    font-family: "Open Sans", sans-serif;
    font-size: 15px;
    letter-spacing: 1.2px;
    color: var(--text-soft);
  }
  /* Back */
  .card-back .brand-block {
    position: absolute; left: 40px; top: 0; height: 280px; width: 270px;
    display: flex; align-items: center; justify-content: center;
  }
  .card-back .brand-name { font-size: 22px; letter-spacing: 2px; }
  .divider {
    position: absolute; left: 322px; top: 74px;
    width: 1px; height: 150px; background: var(--divider);
  }
  .contact-block {
    position: absolute; left: 344px; top: 62px; width: 260px;
  }
  .person-name {
    font-family: "Montserrat", sans-serif; font-weight: 700;
    font-size: 19px; letter-spacing: 1.5px; text-transform: uppercase;
  }
  .person-role {
    font-family: "Montserrat", sans-serif; font-weight: 600;
    font-size: 12px; letter-spacing: .8px; color: var(--text-soft);
    margin-bottom: 14px;
  }
  .contact-list { list-style: none; }
  .contact-list li {
    display: flex; align-items: center; gap: 8px;
    font-family: "Open Sans", sans-serif; font-size: 12.5px;
    color: var(--text-soft); line-height: 21px;
  }
  .contact-list svg { width: 10px; height: 10px; flex: none; fill: var(--text-soft); }
  .address-band {
    position: absolute; left: 0; right: 0; bottom: 0; height: 46px;
    background: var(--band-blue);
    border-top: 3px solid var(--card);
    display: flex; align-items: center; justify-content: center;
    font-family: "Open Sans", sans-serif; font-size: 14px; letter-spacing: .3px;
    color: var(--text-light);
  }
  .address-rule {
    position: absolute; left: 0; right: 0; bottom: 49px; height: 2px;
    background: var(--text-soft);
  }
</style>
</head>
<body>
<main class="stage">
  <section class="card card-front">
    <div class="map-area" role="img" aria-label="Faint world map backdrop"></div>
    <div class="front-content">
      <p class="brand-name">Halvern Consulting</p>
      <p class="tagline">Providing leadership, delivering success</p>
    </div>
  </section>

  <section class="card card-back">
    <div class="map-area" role="img" aria-label="Faint dotted world map backdrop"></div>
    <div class="brand-block">
      <p class="brand-name">Halvern Consulting</p>
    </div>
    <div class="divider"></div>
    <div class="contact-block">
      <p class="person-name">Daniel Ashby</p>
      <p class="person-role">Design Consultant</p>
      <ul class="contact-list">
        <li><svg viewBox="0 0 10 10"><rect x="2" y="0" width="6" height="10" rx="1"/></svg>555-014-2290</li>
        <li><svg viewBox="0 0 10 10"><path d="M2 0l2 2-1 2c1 1 2 2 3 3l2-1 2 2-1 2C4 10 0 6 0 1z"/></svg>01632 960418 (Northgate)</li>
        <li><svg viewBox="0 0 10 10"><path d="M2 0l2 2-1 2c1 1 2 2 3 3l2-1 2 2-1 2C4 10 0 6 0 1z"/></svg>01632 960577 (Eastfield)</li>
        <li><svg viewBox="0 0 10 10"><path d="M0 2h10v6H0z M0 2l5 3 5-3" stroke="#3c3d3f" stroke-width=".8"/></svg>info@halvernconsulting.com</li>
        <li><svg viewBox="0 0 10 10"><circle cx="5" cy="5" r="5"/></svg>www.halvernconsulting.com</li>
      </ul>
    </div>
    <div class="address-rule"></div>
    <div class="address-band">Unit 8, The Linden Centre, Ashgrove Park, Northgate, NG4 7RP</div>
  </section>
</main>
</body>
</html>
```